Garlic Farm for Farm Sales/Restaurant sales

Need a professional, but appealing to agriculture world. We are selling 27 kinds of Organic Garlic from a farm in Simla,CO. I have uploaded logo and business information-we are going to need a template, because I will need to use it for four separate people.
-We are trying to appeal to Farm to table restaurants
-As well as growers/farmers

Target Market(s)

Agriculture Sales/Restaurants-Organic

Industry/Entity Type

Agriculture

Contact Information for Business Card

Want it to look more unique then your average kelto stock card- I want it to look amazing

Font styles to use
Sans Serif

Colors
0455a3
ec1f27
fbed22
ffffff

Requirements
Must have
• Just be creative
Nice to have
• Colorful
Should not have
• plain

```html
<!DOCTYPE html>
<html lang="en">
<head>
<meta charset="utf-8">
<title>Prairie Clove – Business Cards</title>
<link rel="stylesheet" href="https://fonts.googleapis.com/css2?family=Open+Sans:wght@400;600;700&family=Arimo:wght@400&display=swap">
<style>
  :root {
    --navy: #1f2f6b;
    --red: #e3202a;
    --yellow: #fbed22;
    --white: #ffffff;
    --ink: #1a1a1a;
    --backdrop: #8e8782;
  }
  * { box-sizing: border-box; margin: 0; padding: 0; }
  html, body { width: 1200px; height: 864px; overflow: hidden; }
  body {
    background: var(--backdrop);
    display: flex;
    flex-direction: column;
    align-items: center;
    justify-content: center;
    gap: 24px;
    font-family: "Open Sans", sans-serif;
  }
  .card {
    width: 700px;
    height: 400px;
    background: var(--white);
    position: relative;
    overflow: hidden;
    box-shadow: 0 4px 14px rgba(0,0,0,0.18);
  }

  /* Brand colour bands */
  .color-band {
    position: absolute;
    left: 0; right: 0; bottom: 0;
    height: 16px;
    display: flex;
  }
  .color-band span { flex: 1; }
  .band-navy { background: var(--navy); }
  .band-red { background: var(--red); }
  .band-yellow { background: var(--yellow); }
  .side-bar {
    position: absolute;
    top: 0; left: 0; bottom: 16px;
    width: 16px;
    background: var(--navy);
  }
  .top-rule {
    position: absolute;
    top: 0; left: 0; right: 0;
    height: 6px;
    background: var(--yellow);
  }

  /* Front */
  .card-front {
    display: flex;
    flex-direction: column;
    align-items: center;
    justify-content: center;
  }
  .brand-lockup {
    display: flex;
    align-items: center;
    gap: 22px;
  }
  .brand-dot {
    width: 74px; height: 74px;
    border-radius: 50%;
    background: var(--red);
  }
  .brand-name {
    font-family: "Open Sans", sans-serif;
    font-weight: 600;
    color: var(--navy);
    font-size: 58px;
    letter-spacing: 2px;
    text-transform: uppercase;
  }
  .front-rule {
    margin-top: 26px;
    width: 420px;
    height: 6px;
    background: var(--yellow);
  }

  /* Back */
  .card-back .brand-lockup {
    position: absolute;
    top: 62px;
    right: 58px;
    gap: 14px;
  }
  .card-back .brand-dot { width: 56px; height: 56px; }
  .card-back .brand-name { font-size: 40px; letter-spacing: 1px; text-transform: none; }

  .person {
    position: absolute;
    left: 58px;
    top: 196px;
  }
  .person-name {
    font-family: "Arimo", sans-serif;
    color: var(--red);
    font-size: 29px;
    letter-spacing: 0.5px;
    text-transform: uppercase;
    margin-bottom: 14px;
  }
  .address {
    font-style: normal;
    color: var(--ink);
    font-size: 21px;
    line-height: 1.3;
    text-align: right;
  }
  .divider {
    position: absolute;
    left: 372px;
    top: 242px;
    width: 2px;
    height: 96px;
    background: var(--ink);
  }
  .contact-list {
    position: absolute;
    left: 396px;
    top: 238px;
    list-style: none;
  }
  .contact-list li {
    display: flex;
    align-items: center;
    gap: 12px;
    color: var(--ink);
    font-size: 21px;
    line-height: 26px;
  }
  .contact-icon {
    width: 20px; height: 20px;
    border-radius: 4px;
    background: var(--red);
    display: flex;
    align-items: center;
    justify-content: center;
    flex: none;
  }
  .contact-icon svg { width: 14px; height: 14px; }
</style>
</head>
<body>

  <section class="card card-front" aria-label="Card front">
    <div class="top-rule"></div>
    <div class="brand-lockup">
      <span class="brand-dot"></span>
      <span class="brand-name">Prairie Clove</span>
    </div>
    <div class="front-rule"></div>
    <div class="color-band"><span class="band-navy"></span><span class="band-red"></span><span class="band-yellow"></span></div>
  </section>

  <section class="card card-back" aria-label="Card back">
    <div class="side-bar"></div>
    <div class="brand-lockup">
      <span class="brand-dot"></span>
      <span class="brand-name">Prairie Clove</span>
    </div>

    <div class="person">
      <p class="person-name">Daniel Whitcombe</p>
      <address class="address">418 Ridgeway Lane<br>Elbert TX 75119</address>
    </div>

    <div class="divider"></div>

    <ul class="contact-list">
      <li>
        <span class="contact-icon">
          <svg viewBox="0 0 14 14" fill="none" stroke="#fff" stroke-width="1.4" stroke-linejoin="round">
            <path d="M3 2h2.5l1 2.8-1.4 1a6 6 0 0 0 3.1 3.1l1-1.4 2.8 1V11a1 1 0 0 1-1 1A9 9 0 0 1 2 3a1 1 0 0 1 1-1z"/>
          </svg>
        </span>
        555-310-4821
      </li>
      <li>
        <span class="contact-icon">
          <svg viewBox="0 0 14 14" fill="none" stroke="#fff" stroke-width="1.3">
            <rect x="4" y="1.5" width="6" height="3.5"/>
            <rect x="1.5" y="5" width="11" height="5" rx="0.8"/>
            <rect x="4" y="8.5" width="6" height="4"/>
          </svg>
        </span>
        555-310-4827
      </li>
      <li>
        <span class="contact-icon">
          <svg viewBox="0 0 14 14" fill="none" stroke="#fff" stroke-width="1.3" stroke-linejoin="round">
            <rect x="1.5" y="3" width="11" height="8"/>
            <path d="M1.5 3l5.5 4.5L12.5 3M1.5 11l4-4M12.5 11l-4-4"/>
          </svg>
        </span>
        dan@prairieclove.com
      </li>
      <li>
        <span class="contact-icon">
          <svg viewBox="0 0 14 14" fill="none" stroke="#fff" stroke-width="1.2">
            <circle cx="7" cy="7" r="5.5"/>
            <ellipse cx="7" cy="7" rx="2.3" ry="5.5"/>
            <path d="M1.5 7h11M2.5 4.2h9M2.5 9.8h9"/>
          </svg>
        </span>
        www.prairieclove.com
      </li>
    </ul>

    <div class="color-band"><span class="band-navy"></span><span class="band-red"></span><span class="band-yellow"></span></div>
  </section>

</body>
</html>
```